Harborline Auto LLC

Car Dealer Customer Service
Address: 2874 Cresthaven Road, Shelbyville, TN 37162
web: www.harborlineautoxq.net
email: harborlineautoxq@mailnest.example
Phone: (931) 555-0148
Phone: (629) 555-0173

```html
<!DOCTYPE html>
<html lang="en">
<head>
<meta charset="utf-8">
<title>Harborline Auto – Business Card</title>
<link href="https://fonts.googleapis.com/css2?family=Montserrat:wght@700&family=Roboto:wght@400;500&display=swap" rel="stylesheet">
<style>
  :root {
    --backdrop: #3d3d3d;
    --card: #161616;
    --card-deep: #111111;
    --brand-blue: #1f87c7;
    --accent-orange: #f2a93b;
    --text-light: #f2f2f2;
    --emboss: #2a2a2a;
  }
  * { box-sizing: border-box; margin: 0; padding: 0; }
  html, body {
    width: 1200px; height: 801px; overflow: hidden;
    background: var(--backdrop);
  }
  .canvas {
    width: 1200px; height: 801px;
    display: flex; align-items: center; justify-content: center; gap: 20px;
  }
  .card {
    position: relative;
    width: 570px; height: 326px;
    background: var(--card);
    border-bottom: 3px solid var(--brand-blue);
    overflow: hidden;
  }
  .brand-name {
    font-family: "Montserrat", sans-serif;
    font-weight: 700;
    color: var(--brand-blue);
    letter-spacing: 0.5px;
    text-transform: uppercase;
    white-space: nowrap;
  }

  /* Contact side */
  .card-contact .brand-block {
    position: absolute; left: 22px; top: 140px;
    display: flex; align-items: center; gap: 10px;
  }
  .card-contact .brand-dot {
    width: 36px; height: 36px; border-radius: 50%;
    background: var(--brand-blue); flex: none;
  }
  .card-contact .brand-name { font-size: 18px; }
  .divider {
    position: absolute; left: 290px; top: 0; width: 2px; height: 100%;
    background: var(--brand-blue);
  }
  .contact {
    position: absolute; left: 308px; top: 60px; right: 12px;
    font-family: "Roboto", sans-serif; color: var(--text-light);
    font-size: 12.5px; line-height: 1.6;
  }
  .contact .role {
    font-weight: 500; color: var(--brand-blue); font-size: 14px; margin-bottom: 4px;
  }
  .contact .address { margin-bottom: 10px; }
  .contact ul { list-style: none; }
  .contact li { display: flex; align-items: center; gap: 7px; white-space: nowrap; }
  .contact li svg { width: 11px; height: 11px; flex: none; fill: var(--accent-orange); }

  /* Front side */
  .card-front { background: linear-gradient(160deg, var(--card) 0%, var(--card-deep) 100%); }
  .card-front .emboss {
    position: absolute; left: -60px; top: 20px;
    width: 300px; height: 300px; border-radius: 50%;
    background: radial-gradient(circle at 40% 35%, #3a3a3a 0%, var(--emboss) 60%, #1c1c1c 100%);
  }
  .card-front .brand-name {
    position: absolute; right: 30px; top: 176px; font-size: 28px;
  }
</style>
</head>
<body>
<main class="canvas">
  <section class="card card-contact" aria-label="Business card, contact side">
    <div class="brand-block">
      <span class="brand-dot"></span>
      <span class="brand-name">Harborline Auto</span>
    </div>
    <span class="divider"></span>
    <div class="contact">
      <p class="role">Car Dealer Customer Service</p>
      <p class="address">2874 Cresthaven Road<br>Shelbyville, TN 37162</p>
      <ul>
        <li><svg viewBox="0 0 24 24"><path d="M6.6 10.8a15 15 0 0 0 6.6 6.6l2.2-2.2a1 1 0 0 1 1-.25 11.4 11.4 0 0 0 3.6.57 1 1 0 0 1 1 1V20a1 1 0 0 1-1 1A17 17 0 0 1 3 4a1 1 0 0 1 1-1h3.5a1 1 0 0 1 1 1c0 1.25.2 2.450.57 3.57a1 1 0 0 1-.25 1z"/></svg>(931) 555-0148</li>
        <li><svg viewBox="0 0 24 24"><path d="M6.6 10.8a15 15 0 0 0 6.6 6.6l2.2-2.2a1 1 0 0 1 1-.25 11.4 11.4 0 0 0 3.6.57 1 1 0 0 1 1 1V20a1 1 0 0 1-1 1A17 17 0 0 1 3 4a1 1 0 0 1 1-1h3.5a1 1 0 0 1 1 1c0 1.25.2 2.450.57 3.57a1 1 0 0 1-.25 1z"/></svg>(629) 555-0173</li>
        <li><svg viewBox="0 0 24 24"><path d="M2 5h20v14H2z M2 5l10 8 10-8" /></svg>harborlineautoxq@mailnest.example</li>
        <li><svg viewBox="0 0 24 24"><circle cx="12" cy="12" r="10"/></svg>www.harborlineautoxq.net</li>
      </ul>
    </div>
  </section>

  <section class="card card-front" aria-label="Business card, front side">
    <div class="emboss" role="img" aria-label="Embossed brand decoration area"></div>
    <span class="brand-name">Harborline Auto</span>
  </section>
</main>
</body>
</html>
```